Calvera fine stockings - sexy cardboard box design needed!

We need a packaging design for a new online company based in Sydney called 'Calvera Hosiery'. We will be selling sexy stockings to our customers by Italian designers. We mainly feature lace stockings, an example of which, can be seen here:
http://www.brontevassipelli.example/italy-FASHION-WINTER

The design should be a cardboard pull out box, black in colour with the logo on the cover. We are looking for the logo to communicate sophistication and sexiness.

Examples of cardboard box shapes we would like are:
http://www.tradoquel.example/product-gs/583016274/High_quality_drawer_paper_box.html

http://www.tradoquel.example/product-gs/639152487/Cardboard_drawer_box.html

29 December:
I submitted a note when I extended the deadline, but cannot see it, so will write here for clarification. It has been difficult to choose the best design as the designs submitted were of such high quality. I want to have some people judge the designs, but because of the Christmas Season I have extended the deadline so that this can be done. Thanks.

Target Market(s)

The working professional woman.

Industry/Entity Type

Fashion

Requirements
Must have
• The words "Calvera Hosiery" on the cover of the box.

The box should be a sliding drawer.

The box size should be: (22*15*2.5cm).

Washing instructions and recycling logos on the back of the box. See example of uploaded file.

Nice to have
• It would be nice to have the background of the box a dark colour, maybe charcoal? But we are open to all ideas.
Should not have
• A stock photo on cover of box.

```html
<!DOCTYPE html>
<html lang="en">
<head>
<meta charset="utf-8">
<title>Calvera Hosiery – Box Cover</title>
<link rel="stylesheet" href="https://fonts.googleapis.com/css2?family=Jost:wght@300&display=swap">
<style>
  :root {
    --charcoal: #353033;
    --lace-band: #2a2628;
    --text-white: #f2eeee;
  }
  html, body {
    margin: 0;
    padding: 0;
    overflow: hidden;
    background: var(--charcoal);
  }
  .box-cover {
    position: relative;
    width: 817px;
    height: 1200px;
    background: var(--charcoal);
    overflow: hidden;
  }
  .lace-band {
    position: absolute;
    left: 516px;
    top: 0;
    width: 178px;
    height: 1200px;
    background: linear-gradient(90deg, var(--charcoal) 0%, var(--lace-band) 12%, var(--lace-band) 88%, var(--charcoal) 100%);
  }
  .vertical-text {
    position: absolute;
    margin: 0;
    writing-mode: vertical-rl;
    transform: rotate(180deg);
    line-height: 1;
    white-space: nowrap;
    font-family: "Jost", sans-serif;
    font-weight: 300;
    color: var(--text-white);
  }
  .brand-name {
    left: 566px;
    bottom: 83px;
    font-size: 80px;
    letter-spacing: 0.1em;
  }
  .tagline {
    left: 594px;
    bottom: 527px;
    font-size: 28px;
    letter-spacing: 0.21em;
  }
</style>
</head>
<body>
  <main class="box-cover">
    <div class="lace-band" role="img" aria-label="Vertical band of black lace pattern"></div>
    <h1 class="vertical-text brand-name">CALVERA</h1>
    <p class="vertical-text tagline">SHEER SILKY STOCKINGS</p>
  </main>
</body>
</html>
```